Business card for a Exhibition booth fabrication company

Hi. My company would like to change our corporate name card. We are an events and Exhibition stand builder company. We would like our corporate name card to resonate what we do. I need someone to create something unique that relates to the industry that I am in. The graphic designer should be creative to incorporate the elements of my industry and try to blend in well in the design of the card. Our aim is to ensure that we are unique and our card can look different from our competitors.
Updates

Target Market(s)

Marketing and events manager from all companies

Contact Information for Business Card

The business card should have the following details:
Name
Job Title
Email
Website

Colors

Designer to choose colors to be used in the design.

Requirements
Must have
• The card must be look something that is relevant to the service that I am providing. My website is: www.velmora-buildworks.com
• You can see my website to get more information on what service that I am doing
Nice to have
• On the back of my card, I would like to have a globe image with the incorporation of my company logo. This is to indicate that my services can be done in any part of the world.

```html
<!DOCTYPE html>
<html lang="en">
<head>
<meta charset="utf-8">
<title>Velmora Buildworks – Business Card</title>
<link href="https://fonts.googleapis.com/css2?family=Questrial&display=swap" rel="stylesheet">
<style>
  :root {
    --stage: #f1f1f1;
    --card: #ffffff;
    --slate: #656667;
    --signal-red: #ec1c24;
    --ink: #5a5a5a;
    --map-blush: #fcd2c4;
    --shadow: rgba(0,0,0,0.22);
  }
  html, body {
    margin: 0;
    padding: 0;
    width: 1200px;
    height: 1000px;
    overflow: hidden;
    background: var(--stage);
    font-family: "Questrial", "Century Gothic", sans-serif;
  }
  .canvas {
    position: relative;
    width: 1200px;
    height: 1000px;
  }
  .card {
    position: absolute;
    background: var(--card);
    box-shadow: 5px 6px 8px var(--shadow);
    overflow: hidden;
  }
  .card--front { left: 337px; top: 156px; width: 530px; height: 320px; }
  .card--back  { left: 337px; top: 526px; width: 526px; height: 318px; }

  .front-art { position: absolute; inset: 0; }

  .identity {
    position: absolute;
    left: 60px;
    top: 120px;
    width: 250px;
    text-align: center;
    color: #fff;
  }
  .identity__name { font-size: 44px; line-height: 1; margin: 0; font-weight: 400; }
  .identity__title { font-size: 24px; line-height: 1; margin: 8px 0 0; font-weight: 400; }

  .brand-front {
    position: absolute;
    right: 14px;
    top: 44px;
    color: var(--signal-red);
    font-size: 30px;
    line-height: 1.1;
    text-align: right;
  }

  .contact {
    position: absolute;
    right: 10px;
    top: 258px;
    margin: 0;
    padding: 0;
    list-style: none;
    color: var(--ink);
    font-size: 14px;
  }
  .contact li { display: flex; align-items: center; justify-content: flex-end; gap: 8px; height: 23px; }
  .contact svg { width: 12px; height: 10px; }

  .world-map {
    position: absolute;
    left: 53px;
    top: 34px;
    width: 422px;
    height: 252px;
    background: radial-gradient(ellipse at 50% 45%, var(--map-blush) 0%, #fde3da 70%, rgba(255,255,255,0) 100%);
  }
  .brand-back {
    position: absolute;
    left: 0;
    right: 0;
    top: 190px;
    display: flex;
    align-items: center;
    justify-content: center;
    gap: 12px;
  }
  .brand-back__dot {
    width: 18px;
    height: 18px;
    border-radius: 50%;
    background: var(--signal-red);
  }
  .brand-back__name {
    color: var(--ink);
    font-size: 22px;
    letter-spacing: 2px;
  }
</style>
</head>
<body>
<main class="canvas">
  <section class="card card--front" aria-label="Business card front">
    <svg class="front-art" viewBox="0 0 530 320" aria-hidden="true">
      <polygon points="0,0 438,0 246,320 0,320" fill="var(--slate)"/>
      <polygon points="0,103 346,103 306,217 0,217" fill="var(--signal-red)"/>
      <polygon points="346,103 376,103 308,217 306,217" fill="var(--card)"/>
    </svg>
    <div class="identity">
      <p class="identity__name">Name</p>
      <p class="identity__title">Job Title</p>
    </div>
    <div class="brand-front">Velmora<br>Buildworks</div>
    <ul class="contact">
      <li>
        <svg viewBox="0 0 12 10" aria-hidden="true"><rect x="0.5" y="0.5" width="11" height="9" fill="none" stroke="var(--ink)"/><polyline points="0.5,0.5 6,5.5 11.5,0.5" fill="none" stroke="var(--ink)"/></svg>
        info@velmora-buildworks.com
      </li>
      <li>
        <svg viewBox="0 0 12 10" aria-hidden="true"><circle cx="6" cy="5" r="4.5" fill="var(--ink)"/></svg>
        www.velmora-buildworks.com
      </li>
    </ul>
  </section>

  <section class="card card--back" aria-label="Business card back">
    <div class="world-map" role="img" aria-label="World map in soft blush tone showing global reach"></div>
    <div class="brand-back">
      <span class="brand-back__dot" aria-hidden="true"></span>
      <span class="brand-back__name">VELMORA BUILDWORKS</span>
    </div>
  </section>
</main>
</body>
</html>
```